Property management company looking for modern card design

We at Blue Heron Partners provides property management services for its residential and commercial properties, with expertise in all categories of multifamily, industrial and office projects throughout California.

We need a business card design that is professional and modern designed business card. In our field, clients get hundreds of business cards, we would like our card to stand out.

Please avoid small print.

Target Market(s)

Professionals and high end clients

Industry/Entity Type

Financial Planning

Contact Information for Business Card

Company Name: Blue Heron Partners, Name, email, license #, phone number, website blueheronpartners.com

Font styles to use
Sans Serif

Requirements
Must have
• The card design needs to be adaptable because there is a possibly we will be expanding into different sectors other than real estate. The card design should be focused on financial planning and asset management.
Nice to have
• Modern and simple business card. Eye catching. Non-standard size/shaped cards would be great.
• blueheronpartners.com
Should not have
• Too many bright color or any pictures or shapes of real estate stuff.

```html
<!DOCTYPE html>
<html lang="en">
<head>
<meta charset="utf-8">
<title>Blue Heron Partners — Business Card</title>
<link href="https://fonts.googleapis.com/css2?family=Roboto:wght@400;500&display=swap" rel="stylesheet">
<style>
  :root {
    --backdrop: #e6e4e0;
    --kraft: #ad9374;
    --kraft-dark: #a48a6b;
    --ink: #2f2f30;
    --rule: #1f1f1f;
  }
  html, body {
    margin: 0;
    padding: 0;
    width: 1200px;
    height: 1000px;
    overflow: hidden;
    background: var(--backdrop);
    font-family: "Roboto", Arial, sans-serif;
  }
  .canvas {
    position: relative;
    width: 1200px;
    height: 1000px;
  }
  .card {
    position: absolute;
    left: 288px;
    width: 625px;
    height: 357px;
    background: radial-gradient(ellipse at 50% 40%, var(--kraft) 0%, var(--kraft-dark) 100%);
    box-shadow: 0 3px 10px rgba(0,0,0,0.25);
    color: var(--ink);
  }
  .card--front { top: 140px; }
  .card--back { top: 531px; }

  .wordmark {
    position: absolute;
    left: 0;
    right: 0;
    text-align: center;
    font-weight: 400;
    color: var(--ink);
    white-space: nowrap;
  }
  .card--front .wordmark {
    top: 158px;
    font-size: 44px;
    letter-spacing: 0.5px;
  }
  .card--back .wordmark {
    top: 50px;
    font-size: 30px;
    letter-spacing: 0.3px;
  }

  .details {
    position: absolute;
    left: 165px;
    top: 119px;
    width: 294px;
    height: 191px;
  }
  .details__divider {
    position: absolute;
    left: 90px;
    top: 0;
    width: 1px;
    height: 191px;
    background: var(--rule);
  }
  .details__row {
    position: absolute;
    left: 0;
    width: 294px;
    height: 37px;
    font-size: 14.5px;
    line-height: 37px;
  }
  .details__row--ruled { border-bottom: 1px solid var(--rule); }
  .details__label {
    position: absolute;
    right: 220px;
    text-align: right;
  }
  .details__value {
    position: absolute;
    left: 104px;
  }
</style>
</head>
<body>
<main class="canvas">
  <section class="card card--front" aria-label="Card front">
    <div class="wordmark">Blue Heron Partners</div>
  </section>

  <section class="card card--back" aria-label="Card back">
    <div class="wordmark">Blue Heron Partners</div>
    <div class="details">
      <div class="details__divider"></div>
      <div class="details__row details__row--ruled" style="top:3px">
        <span class="details__label">Name</span>
        <span class="details__value">Daniel Marsh</span>
      </div>
      <div class="details__row details__row--ruled" style="top:40px">
        <span class="details__label">License</span>
        <span class="details__value">#618204417</span>
      </div>
      <div class="details__row details__row--ruled" style="top:78px">
        <span class="details__label">Phone</span>
        <span class="details__value">555-0142-7731</span>
      </div>
      <div class="details__row details__row--ruled" style="top:117px">
        <span class="details__label">Email</span>
        <span class="details__value">info@blueheronpartners.com</span>
      </div>
      <div class="details__row" style="top:155px">
        <span class="details__label">Website</span>
        <span class="details__value">www.blueheronpartners.com</span>
      </div>
    </div>
  </section>
</main>
</body>
</html>
```